K&R Trailer Rental promo Flyer 5.5x8.5" Flyer

All assets and several pictures of my trailers, that we rent out, are attached.

Flyer dimensions are 5.5"x8.5" - I'll be having it printed on glossy stock.
The dimensions and capacity of the trailers is key.
Include phone number: 555-613-2890 and our website kandrtrailer-example.com

I want something that will really "POP".

Target Market(s)

Blue collar business owners. Recreational offer roads/4x4 folks, used car dealers, contractors/small business owners. Folks with only occasional need for a trailer

Industry/Entity Type

Trailer Rental

Font styles to use
Other font styles liked:
• Designer's choice/no preference

Colors
EE7325
F08F49
F5BC92
FAE3D3
FDF4ED

Requirements
Must have
• Phone number, website, and details about our trailer offerings

```html
<!DOCTYPE html>
<html lang="en">
<head>
<meta charset="utf-8">
<title>K&amp;R Trailer Rental – Promo Flyer</title>
<link href="https://fonts.googleapis.com/css2?family=Archivo+Black&family=Poppins:wght@400;600&display=swap" rel="stylesheet">
<style>
  :root {
    --stage: #e9e9e9;
    --ink-dark: #1f2224;
    --ink-darker: #151718;
    --orange: #ee7325;
    --orange-mid: #f08f49;
    --peach: #f5bc92;
    --cream: #fae3d3;
    --cream-light: #fdf4ed;
    --white: #ffffff;
    --text-dark: #2a2a2a;
  }
  * { box-sizing: border-box; margin: 0; padding: 0; }
  html, body { width: 1196px; height: 1200px; overflow: hidden; background: var(--stage); }
  .flyer {
    position: absolute; left: 228px; top: 28px;
    width: 740px; height: 1144px;
    background: var(--ink-dark); overflow: hidden;
    font-family: "Poppins", sans-serif;
  }
  .flyer__hero { position: absolute; left: 0; top: 0; width: 740px; height: 560px; }
  .brand {
    position: absolute; left: 0; top: 330px; width: 260px; height: 96px;
    background: var(--cream-light); border-radius: 0 48px 48px 0;
    display: flex; align-items: center; gap: 12px; padding-left: 22px;
  }
  .brand__dot { width: 16px; height: 16px; border-radius: 50%; background: var(--orange); flex: none; }
  .brand__name {
    font-family: "Archivo Black", sans-serif; font-size: 20px; line-height: 1.1;
    color: var(--text-dark);
  }
  .side-tab {
    position: absolute; right: 0; top: 570px; width: 26px; height: 150px;
    background: var(--orange-mid); border-radius: 10px 0 0 10px;
  }
  .headline {
    position: absolute; left: 28px; top: 560px;
    font-family: "Archivo Black", sans-serif; color: var(--orange);
  }
  .headline__main { font-size: 62px; line-height: 1; }
  .headline__sub { font-size: 32px; line-height: 1.1; margin-left: 170px; margin-top: 4px; }
  .offer {
    position: absolute; left: 28px; top: 680px; width: 680px;
    font-family: "Archivo Black", sans-serif; color: var(--peach);
    font-size: 25px; line-height: 1.12;
  }
  .uses { position: absolute; list-style: none; font-family: "Archivo Black", sans-serif; color: var(--white); font-size: 22px; line-height: 1.45; }
  .uses li { display: flex; align-items: center; gap: 12px; }
  .uses svg { width: 20px; height: 16px; flex: none; }
  .uses--left { left: 28px; top: 752px; }
  .uses--right { left: 420px; top: 752px; }
  .perks-panel {
    position: absolute; left: 0; top: 840px; width: 400px; height: 190px;
    background: linear-gradient(90deg, var(--cream) 82%, rgba(250,227,211,0) 100%);
  }
  .perks { position: absolute; left: 34px; top: 852px; list-style: disc; padding-left: 16px; color: var(--text-dark); font-size: 17px; line-height: 1.55; }
  .specs {
    position: absolute; left: 420px; top: 842px; width: 300px;
    color: var(--white); list-style: none;
  }
  .specs__title { font-family: "Archivo Black", sans-serif; color: var(--orange-mid); font-size: 18px; margin-bottom: 6px; }
  .specs__item { font-size: 15px; font-weight: 600; line-height: 1.5; }
  .specs__item b { color: var(--peach); font-weight: 600; }
  .photo-rv {
    position: absolute; left: 0; top: 1030px; width: 300px; height: 114px;
    background: linear-gradient(180deg, #cfd3d6 0%, #9ea4a9 55%, #2a2d33 100%);
  }
  .photo-flatbed {
    position: absolute; left: 400px; top: 940px; width: 340px; height: 120px;
    background: linear-gradient(160deg, #2a2a2c 0%, #b39874 45%, #3b3b3d 80%, var(--ink-darker) 100%);
    clip-path: polygon(10% 0, 100% 20%, 100% 100%, 0 100%);
  }
  .contact {
    position: absolute; left: 300px; top: 1030px; width: 440px; height: 114px;
    background: var(--orange); color: var(--white);
    font-family: "Archivo Black", sans-serif;
  }
  .call-tag {
    position: absolute; left: 300px; top: 1000px; height: 40px;
    display: flex; align-items: center;
  }
  .call-tag__icon { width: 40px; height: 40px; background: var(--cream); display: flex; align-items: center; justify-content: center; }
  .call-tag__label { background: var(--orange-mid); border: 3px solid var(--ink-dark); color: var(--white); font-family: "Archivo Black", sans-serif; font-size: 17px; padding: 4px 14px; }
  .contact__row { position: absolute; right: 40px; display: flex; align-items: center; gap: 12px; }
  .contact__row--phone { top: 34px; font-size: 26px; }
  .contact__row--web { top: 72px; font-size: 21px; }
</style>
</head>
<body>
<main class="flyer">
  <svg class="flyer__hero" viewBox="0 0 740 560">
    <defs>
      <linearGradient id="heroPhotoTone" x1="0" y1="0" x2="0" y2="1">
        <stop offset="0" stop-color="#5d7da6"/>
        <stop offset="0.45" stop-color="#3d5a3c"/>
        <stop offset="0.75" stop-color="#6e7a52"/>
        <stop offset="1" stop-color="#8b8a84"/>
      </linearGradient>
    </defs>
    <rect width="740" height="560" fill="var(--ink-dark)"/>
    <path d="M0 0 H740 V90 C520 40 260 60 0 150 Z" fill="var(--orange)"/>
    <path d="M0 470 C200 560 480 560 740 420 V470 C480 600 200 600 0 505 Z" fill="var(--orange)"/>
    <path d="M0 455 C200 545 480 545 740 405 V430 C480 570 200 570 0 480 Z" fill="var(--peach)"/>
    <path d="M0 150 C260 60 520 40 740 90 V110 C520 70 260 85 0 175 Z" fill="var(--peach)"/>
    <path role="img" aria-label="Photo: two cars loaded on a long flatbed car trailer hitched to an SUV in a residential driveway" d="M0 175 C260 85 520 70 740 110 V405 C480 545 200 545 0 455 Z" fill="url(#heroPhotoTone)"/>
  </svg>

  <div class="brand">
    <span class="brand__dot"></span>
    <span class="brand__name">K&amp;R TRAILER<br>RENTAL</span>
  </div>

  <div class="side-tab"></div>

  <h1 class="headline">
    <div class="headline__main">NEED A TRAILER?</div>
    <div class="headline__sub">WE’VE GOT YOU COVERED!</div>
  </h1>

  <p class="offer">WE OFFER CAR &amp; EQUIPMENT TRAILERS FOR<br>ALL TYPES OF JOBS:</p>

  <ul class="uses uses--left">
    <li><svg viewBox="0 0 20 16"><path d="M0 0 L20 8 L0 16 L5 8 Z" fill="#fff"/></svg>Moving vehicles</li>
    <li><svg viewBox="0 0 20 16"><path d="M0 0 L20 8 L0 16 L5 8 Z" fill="#fff"/></svg>Hauling equipment</li>
  </ul>
  <ul class="uses uses--right">
    <li><svg viewBox="0 0 20 16"><path d="M0 0 L20 8 L0 16 L5 8 Z" fill="#fff"/></svg>Construction projects</li>
    <li><svg viewBox="0 0 20 16"><path d="M0 0 L20 8 L0 16 L5 8 Z" fill="#fff"/></svg>DIY &amp; home projects</li>
  </ul>

  <div class="perks-panel"></div>
  <ul class="perks">
    <li>Clean, well-maintained trailers</li>
    <li>Short or long-term</li>
    <li>Affordable rates</li>
    <li>Fast &amp; easy booking</li>
    <li>Friendly, local service</li>
  </ul>

  <ul class="specs">
    <li class="specs__title">TRAILER SIZES &amp; CAPACITY</li>
    <li class="specs__item"><b>Car hauler:</b> 20 ft deck · 7,000 lb</li>
    <li class="specs__item"><b>Equipment:</b> 18 ft deck · 10,000 lb</li>
  </ul>

  <div class="photo-flatbed" role="img" aria-label="Photo: empty tandem-axle flatbed equipment trailer with wood deck"></div>
  <div class="photo-rv" role="img" aria-label="Photo: vintage motorhome loaded on a car trailer"></div>

  <section class="contact">
    <div class="contact__row contact__row--phone">555-613-2890
      <svg width="22" height="22" viewBox="0 0 24 24"><path d="M6.6 10.8a15.1 15.1 0 0 0 6.6 6.6l2.2-2.2a1 1 0 0 1 1-.25 11.4 11.4 0 0 0 3.6.57 1 1 0 0 1 1 1V20a1 1 0 0 1-1 1A17 17 0 0 1 3 4a1 1 0 0 1 1-1h3.5a1 1 0 0 1 1 1c0 1.25.2 2.45.57 3.57a1 1 0 0 1-.25 1z" fill="#fff"/></svg>
    </div>
    <div class="contact__row contact__row--web">kandrtrailer-example.com
      <svg width="22" height="22" viewBox="0 0 24 24" fill="none" stroke="#fff" stroke-width="2"><circle cx="12" cy="12" r="10"/><path d="M2 12h20M12 2c3 3 3 17 0 20M12 2c-3 3-3 17 0 20"/></svg>
    </div>
  </section>

  <div class="call-tag">
    <span class="call-tag__icon"><svg width="22" height="22" viewBox="0 0 24 24"><path d="M6.6 10.8a15.1 15.1 0 0 0 6.6 6.6l2.2-2.2a1 1 0 0 1 1-.25 11.4 11.4 0 0 0 3.6.57 1 1 0 0 1 1 1V20a1 1 0 0 1-1 1A17 17 0 0 1 3 4a1 1 0 0 1 1-1h3.5a1 1 0 0 1 1 1c0 1.25.2 2.45.57 3.57a1 1 0 0 1-.25 1z" fill="#1f2224"/></svg></span>
    <span class="call-tag__label">CALL NOW!</span>
  </div>
</main>
</body>
</html>
```